Keystone ridge construction brochure

i would like a brochure that can be send to clients digitally and printed. we are a geotechnical, foundation, and concrete company. I attached info below

Target Market(s)

Construction managers, general contractors, developers, municipalities, private, and commercial partners.

Industry/Entity Type

Geotechnical / foundation

Font styles to use
Serif
Other font styles liked:
• Maybe same as logo

Colors
0054AA
0677BA
7BADD7
CADEEF
E8F1F8

```html
<!DOCTYPE html>
<html lang="en">
<head>
<meta charset="utf-8">
<title>Keystone Ridge Construction – Brochure</title>
<link href="https://fonts.googleapis.com/css2?family=Montserrat:ital,wght@0,300;0,400;0,500;0,600;0,700;0,800;1,500&display=swap" rel="stylesheet">
<style>
  :root{
    --navy:#0f1f40;
    --navy-deep:#0b1733;
    --slate:#4e5d6d;
    --charcoal:#38393d;
    --paper:#ffffff;
    --mist:#f1f1f1;
    --ink:#141414;
    --grey-text:#666a70;
    --steel-photo:#7f848a;
    --orange-photo:#b77a3a;
    --concrete-photo:#8b8c8a;
  }
  *{margin:0;padding:0;box-sizing:border-box}
  html,body{width:1200px;height:767px;overflow:hidden;background:var(--slate)}
  body{font-family:'Montserrat',sans-serif;color:var(--navy);position:relative}
  .page{position:absolute;top:28px;width:550px;height:711px;background:var(--paper);overflow:hidden}
  .page--front{left:34px}
  .page--back{left:616px}
  .abs{position:absolute}

  /* front hero */
  .hero-photo{left:0;top:0;width:550px;height:355px;
    background:linear-gradient(115deg,var(--orange-photo) 0%,#6d5a45 35%,var(--steel-photo) 55%,#a97a56 75%,#6b5646 100%)}
  .hero-logo-plate{left:0;top:0}
  .brand{font-weight:800;color:var(--navy);letter-spacing:.5px;line-height:1}
  .brand--front{left:14px;top:16px;font-size:25px;line-height:27px}
  .hero-panel{left:0;top:0}
  .hero-title{left:11px;top:259px;font-size:28.5px;font-weight:800;color:#fff;line-height:34px;letter-spacing:.6px}
  .hero-sub{left:12px;top:335px;font-size:7.5px;font-weight:600;color:#fff;letter-spacing:.3px}

  .section-title{font-weight:800;color:var(--navy);font-size:19.5px;letter-spacing:.6px;display:flex;align-items:center;gap:12px;white-space:nowrap}
  .section-title svg{width:31px;height:17px;flex:none}
  .services-title{left:0;width:550px;top:370px;justify-content:center}

  .svc-col{top:412px}
  .svc-head{font-size:10.6px;font-weight:700;color:var(--ink);letter-spacing:.3px;white-space:nowrap}
  .check-list{list-style:none;margin-top:18px}
  .check-list li{display:flex;align-items:center;font-size:10.3px;color:var(--ink);height:17.3px;white-space:nowrap}
  .check-list svg{width:9px;height:8px;margin-right:14px;flex:none}

  .values-band{left:0;top:543px;width:550px;height:108px;background:var(--mist)}
  .value{position:absolute;top:20px;width:120px;margin-left:-60px;text-align:center}
  .value-icon{width:43px;height:43px;border:1px solid var(--navy);border-radius:50%;margin:0 auto;background:#fff;display:flex;align-items:center;justify-content:center}
  .value-icon svg{width:26px;height:26px}
  .value-label{font-size:8.7px;color:var(--ink);margin-top:13px;white-space:nowrap}

  .contact-bar{left:0;top:651px;width:550px;height:60px;background:var(--navy)}
  .contact-item{position:absolute;top:16px;display:flex;align-items:center;gap:10px}
  .contact-icon{width:28px;height:28px;background:#fff;display:flex;align-items:center;justify-content:center}
  .contact-icon svg{width:18px;height:18px}
  .contact-label{font-size:7.3px;font-weight:700;color:#fff;letter-spacing:.3px}
  .contact-value{font-size:8.5px;color:#fff;margin-top:5px;font-weight:400}

  /* back page */
  .top-band{left:0;top:0;width:550px;height:260px;background:#f2f2f2}
  .concrete-photo{left:0;top:0}
  .brand--back{left:12px;top:13px;display:flex;align-items:center;gap:8px;font-size:20px}
  .brand-square{width:14px;height:14px;background:var(--navy)}
  .tagline{left:12px;top:53px;font-size:10px;font-style:italic;font-weight:500;color:var(--navy);letter-spacing:.2px}
  .industries-head{left:12px;top:81px;font-size:10.8px;font-weight:700;color:var(--ink);letter-spacing:.3px}
  .industries{left:13px;top:101px;margin:0}
  .industries li{height:21.7px;font-size:12px;color:var(--navy);font-weight:400;letter-spacing:.2px}
  .industries svg{width:10px;height:9px;margin-right:13px}

  .about-title{left:0;width:550px;top:287px;justify-content:center}
  .lead{left:0;width:550px;top:323px;text-align:center;font-size:12px;line-height:19.5px;color:var(--ink);font-weight:500}
  .body-copy{left:0;width:550px;text-align:center;color:var(--grey-text);font-weight:400}
  .about-copy{top:367px;font-size:10.8px;line-height:17.4px}
  .build-title{left:0;width:550px;top:445px;justify-content:center}
  .build-copy{top:480px;font-size:12.3px;line-height:19.5px}
  .commit-title{left:0;width:550px;top:548px;justify-content:center}
  .commit-copy{top:582px;font-size:12.3px;line-height:19.5px}

  .slogan-bar{left:0;top:662px;width:550px;height:49px;background:var(--navy-deep);display:flex;align-items:center;justify-content:center}
  .slogan{font-size:21.5px;font-weight:800;color:#fff;letter-spacing:.5px;white-space:nowrap}
</style>
</head>
<body>

<svg width="0" height="0" style="position:absolute">
  <defs>
    <symbol id="slashes" viewBox="0 0 31 17"><g fill="#0f1f40"><polygon points="4,0 9,0 5,17 0,17"/><polygon points="15,0 20,0 16,17 11,17"/><polygon points="26,0 31,0 27,17 22,17"/></g></symbol>
    <symbol id="tick" viewBox="0 0 10 9"><polyline points="1,4.8 3.8,7.6 9,1.2" fill="none" stroke="#0f1f40" stroke-width="2.2" stroke-linejoin="round"/></symbol>
  </defs>
</svg>

<!-- FRONT PAGE -->
<section class="page page--front">
  <div class="abs hero-photo" role="img" aria-label="Photo: site engineer in hard hat and safety vest inspecting a steel pile beside an excavator on a waterfront job site"></div>

  <svg class="abs hero-logo-plate" width="550" height="100" viewBox="0 0 550 100">
    <polygon points="0,0 241,0 152,82 0,82" fill="#fff"/>
    <polygon points="152,82 241,0 250,0 160,86 0,86 0,82" fill="var(--navy)"/>
  </svg>
  <div class="abs brand brand--front">KEYSTONE<br>RIDGE</div>

  <svg class="abs hero-panel" width="550" height="355" viewBox="0 0 550 355">
    <polygon points="0,245 290,245 367,355 0,355" fill="var(--navy)" opacity=".88"/>
  </svg>
  <h1 class="abs hero-title">BUILDING STRONG<br>FOUNDATIONS.</h1>
  <p class="abs hero-sub">DELIVERING LASTING RESULTS.</p>

  <h2 class="abs section-title services-title"><svg><use href="#slashes"/></svg>OUR SERVICES<svg><use href="#slashes"/></svg></h2>

  <div class="abs svc-col" style="left:12px">
    <h3 class="svc-head">GEOTECHNICAL SERVICES</h3>
    <ul class="check-list">
      <li><svg><use href="#tick"/></svg>Ground Improvement</li>
      <li><svg><use href="#tick"/></svg>Soil Stabilization</li>
      <li><svg><use href="#tick"/></svg>Earth Retention Systems</li>
      <li><svg><use href="#tick"/></svg>Site Preparation</li>
      <li><svg><use href="#tick"/></svg>Excavation Support</li>
    </ul>
  </div>
  <div class="abs svc-col" style="left:185px">
    <h3 class="svc-head">FOUNDATION CONSTRUCTION</h3>
    <ul class="check-list">
      <li><svg><use href="#tick"/></svg>Deep Foundations</li>
      <li><svg><use href="#tick"/></svg>Drilled Shafts</li>
      <li><svg><use href="#tick"/></svg>Helical Piles</li>
      <li><svg><use href="#tick"/></svg>Micropiles</li>
      <li><svg><use href="#tick"/></svg>Spread Footings</li>
    </ul>
  </div>
  <div class="abs svc-col" style="left:376px">
    <h3 class="svc-head">CONCRETE CONSTRUCTION</h3>
    <ul class="check-list">
      <li><svg><use href="#tick"/></svg>Structural Concrete</li>
      <li><svg><use href="#tick"/></svg>Reinforced Concrete</li>
      <li><svg><use href="#tick"/></svg>Concrete Slabs</li>
      <li><svg><use href="#tick"/></svg>Retaining Walls</li>
      <li><svg><use href="#tick"/></svg>Equipment Pads</li>
    </ul>
  </div>

  <div class="abs values-band">
    <div class="value" style="left:51px">
      <div class="value-icon"><svg viewBox="0 0 26 26" fill="none" stroke="#0f1f40" stroke-width="1.3"><circle cx="13" cy="8" r="3"/><circle cx="6" cy="11" r="2.3"/><circle cx="20" cy="11" r="2.3"/><path d="M8 22v-5a5 5 0 0 1 10 0v5z"/><path d="M2 22v-3.5a4 4 0 0 1 5-3.8M24 22v-3.5a4 4 0 0 0-5-3.8"/></svg></div>
      <div class="value-label">Experienced Team</div>
    </div>
    <div class="value" style="left:146px">
      <div class="value-icon"><svg viewBox="0 0 26 26" fill="none" stroke="#0f1f40" stroke-width="1.3"><path d="M13 3l7 3v6c0 4.5-3 7.5-7 9-4-1.5-7-4.5-7-9V6z"/><polyline points="9.5,12 12,14.5 16.5,9.5"/></svg></div>
      <div class="value-label">Safety Approach</div>
    </div>
    <div class="value" style="left:248px">
      <div class="value-icon"><svg viewBox="0 0 26 26" fill="none" stroke="#0f1f40" stroke-width="1.3"><circle cx="13" cy="10" r="7"/><polygon points="13,6.5 14.2,9 17,9.3 15,11.1 15.5,13.8 13,12.5 10.5,13.8 11,11.1 9,9.3 11.8,9"/><path d="M9 16l-2 8 3-2 2 3 1-6M17 16l2 8-3-2-2 3-1-6"/></svg></div>
      <div class="value-label">Quality Workmanship</div>
    </div>
    <div class="value" style="left:366px">
      <div class="value-icon"><svg viewBox="0 0 26 26" fill="none" stroke="#0f1f40" stroke-width="1.3"><rect x="3" y="5" width="20" height="16"/><circle cx="9" cy="11" r="2.5"/><line x1="14" y1="9" x2="20" y2="9"/><line x1="14" y1="13" x2="20" y2="13"/><line x1="6" y1="17" x2="20" y2="17"/></svg></div>
      <div class="value-label">Reliable Project Delivery</div>
    </div>
    <div class="value" style="left:488px">
      <div class="value-icon"><svg viewBox="0 0 26 26" fill="none" stroke="#0f1f40" stroke-width="1.3"><circle cx="12" cy="12" r="3.2"/><path d="M5 22a7 7 0 0 1 12-4"/><circle cx="19.5" cy="19.5" r="3.2"/><polyline points="18,19.5 19.2,20.8 21.2,18.4"/><path d="M6 5l.8 1.6 1.7.2-1.3 1.2.4 1.7-1.6-.9-1.6.9.4-1.7-1.3-1.2 1.7-.2zM13 2.5l.8 1.6 1.7.2-1.3 1.2.4 1.7-1.6-.9-1.6.9.4-1.7-1.3-1.2 1.7-.2zM20 5l.8 1.6 1.7.2-1.3 1.2.4 1.7-1.6-.9-1.6.9.4-1.7-1.3-1.2 1.7-.2z"/></svg></div>
      <div class="value-label">Client-Focused Service</div>
    </div>
  </div>

  <div class="abs contact-bar">
    <svg class="abs" style="left:0;top:-3px" width="550" height="63" viewBox="0 0 550 63">
      <polygon points="158,0 388,0 359,63 128,63" fill="var(--charcoal)"/>
    </svg>
    <div class="contact-item" style="left:12px">
      <div class="contact-icon"><svg viewBox="0 0 24 24"><path fill="#0f1f40" d="M6.6 10.8a15.1 15.1 0 0 0 6.6 6.6l2.2-2.2a1 1 0 0 1 1-.25 11.4 11.4 0 0 0 3.6.57 1 1 0 0 1 1 1V20a1 1 0 0 1-1 1A17 17 0 0 1 3 4a1 1 0 0 1 1-1h3.5a1 1 0 0 1 1 1c0 1.25.2 2.45.57 3.57a1 1 0 0 1-.25 1z"/></svg></div>
      <div><div class="contact-label">PHONE</div><div class="contact-value">+1-888-888-8888</div></div>
    </div>
    <div class="contact-item" style="left:168px">
      <div class="contact-icon"><svg viewBox="0 0 24 24" fill="none" stroke="#0f1f40" stroke-width="1.8"><rect x="3" y="5.5" width="18" height="13"/><polyline points="3,5.5 12,13 21,5.5"/><line x1="3" y1="18.5" x2="10" y2="11.5"/><line x1="21" y1="18.5" x2="14" y2="11.5"/></svg></div>
      <div><div class="contact-label">EMAIL ADDRESS</div><div class="contact-value">info@keystoneridgeconstruction.com</div></div>
    </div>
    <div class="contact-item" style="left:400px">
      <div class="contact-icon"><svg viewBox="0 0 24 24"><path fill="#0f1f40" d="M12 2a7 7 0 0 0-7 7c0 5.2 7 13 7 13s7-7.8 7-13a7 7 0 0 0-7-7zm0 9.6a2.6 2.6 0 1 1 0-5.2 2.6 2.6 0 0 1 0 5.2z"/></svg></div>
      <div><div class="contact-label">LOCATION</div><div class="contact-value">123 Lorem ipsum Dolor</div></div>
    </div>
  </div>
</section>

<!-- BACK PAGE -->
<section class="page page--back">
  <div class="abs top-band"></div>
  <svg class="abs concrete-photo" width="550" height="260" viewBox="0 0 550 260" role="img" aria-label="Photo: worker in red hard hat guiding a concrete pump hose over rebar during a slab pour">
    <defs>
      <linearGradient id="concreteTone" x1="0" y1="0" x2="1" y2="1">
        <stop offset="0" stop-color="#9a9b98"/>
        <stop offset=".5" stop-color="var(--concrete-photo)"/>
        <stop offset="1" stop-color="#6f6a63"/>
      </linearGradient>
    </defs>
    <polygon points="264,0 550,0 550,260 266,260 224,174" fill="var(--navy)"/>
    <polygon points="272,0 550,0 550,260 274,260 232,174" fill="url(#concreteTone)"/>
  </svg>
  <div class="abs brand brand--back"><span class="brand-square"></span>KEYSTONE RIDGE</div>
  <p class="abs tagline">GEOTECHNICAL - FOUNDATION - CONCRETE</p>
  <h3 class="abs industries-head">INDUSTRIES WE SERVE</h3>
  <ul class="abs check-list industries">
    <li><svg><use href="#tick"/></svg>Commercial Construction</li>
    <li><svg><use href="#tick"/></svg>Industrial Facilities</li>
    <li><svg><use href="#tick"/></svg>Municipal Projects</li>
    <li><svg><use href="#tick"/></svg>Residential Developments</li>
    <li><svg><use href="#tick"/></svg>Infrastructure Projects</li>
    <li><svg><use href="#tick"/></svg>Energy Sector</li>
  </ul>

  <h2 class="abs section-title about-title"><svg><use href="#slashes"/></svg>ABOUT KEYSTONE RIDGE CONSTRUCTION<svg><use href="#slashes"/></svg></h2>
  <p class="abs lead">Keystone Ridge Construction is a trusted provider of geotechnical, foundation,<br>and concrete construction services.</p>
  <p class="abs body-copy about-copy">We partner with commercial, industrial, municipal, and residential clients to deliver safe, durable,<br>and high-quality construction solutions. With experienced professionals and modern equipment,<br>we ensure every project is completed efficiently and built to last.</p>

  <h2 class="abs section-title build-title"><svg><use href="#slashes"/></svg>LET'S BUILD YOUR NEXT PROJECT<svg><use href="#slashes"/></svg></h2>
  <p class="abs body-copy build-copy">Whether you're starting a new development, strengthening existing infrastructure, or<br>need specialized geotechnical expertise, Keystone Ridge Construction is ready to help.</p>

  <h2 class="abs section-title commit-title"><svg><use href="#slashes"/></svg>OUR COMMITMENT<svg><use href="#slashes"/></svg></h2>
  <p class="abs body-copy commit-copy">We are committed to delivering construction solutions that combine engineering<br>excellence, precision workmanship, and long-term durability. Every project is built<br>on safety, integrity, and reliability.</p>

  <div class="abs slogan-bar"><p class="slogan">STRONG FOUNDATIONS. TRUSTED RESULTS.</p></div>
</section>

</body>
</html>
```